Design my dad a new business card because his current one sucks!

I need a business card designed for my fathers home maintenance business. His customers are individuals (single moms, old people etc.) as well as the occasional business. As such it needs to be accessible to both target audiences.

The front of the card should be dark grey on yellow with the logo and contain the following information:
- Darren Holtwick
- 0488 274 915
- info@brightoakhomecare.com.au
- 0488 274 915

- ABN: 71 284 630 912
- 'Fully Insured'

The reverse should be yellow on dark grey and will have the web address:
- brightoakhomecare.com.au

And a few key services he offers:
GENERAL REPAIRS
PAINTING/TILING/
PAVING &CONCRETING
PRESSURE WASHING
ON-SITE WELDING
DECKING ADDITIONS & REPAIRS
FENCING
FULL BOND CLEANING

This will be first time the logo has been printed so you will need to come up with the best CMYK approximation of the RGB colours to make sure it is a close as possible.

```html
<!DOCTYPE html>
<html lang="en">
<head>
<meta charset="utf-8">
<title>Bright Oak Home Care – Business Cards</title>
<link href="https://fonts.googleapis.com/css2?family=Open+Sans:wght@400;600;700;800&display=swap" rel="stylesheet">
<style>
  :root {
    --backdrop: #e4e4e2;
    --yellow: #f5c400;
    --grey: #2e2e30;
    --grey-soft: #3a3a3c;
    --rule: rgba(46,46,48,.45);
    --shadow: rgba(0,0,0,.18);
  }
  * { box-sizing: border-box; margin: 0; padding: 0; }
  html, body {
    width: 1200px; height: 1005px; overflow: hidden;
    background: var(--backdrop);
    font-family: "Open Sans", Arial, sans-serif;
    color: var(--grey);
  }
  .canvas { position: relative; width: 1200px; height: 1005px; }

  .card { position: absolute; box-shadow: 0 6px 18px var(--shadow); }

  .brand { display: flex; align-items: center; gap: 14px; }
  .brand-mark { width: 30px; height: 30px; border-radius: 50%; flex: none; }
  .brand-name {
    font-weight: 800; letter-spacing: .5px;
    text-transform: uppercase; line-height: 1.05;
  }

  /* Reverse: yellow on dark grey */
  .card-reverse {
    left: 400px; top: 70px; width: 740px; height: 423px;
    background: var(--grey); color: var(--yellow);
  }
  .card-reverse .brand {
    position: absolute; left: 0; right: 0; top: 78px; justify-content: center;
  }
  .card-reverse .brand-mark { background: var(--yellow); }
  .card-reverse .brand-name { font-size: 40px; color: var(--yellow); }
  .card-reverse .web-address {
    position: absolute; left: 0; right: 0; top: 142px;
    text-align: center; font-size: 18px; font-weight: 600; color: var(--yellow);
  }
  .services {
    position: absolute; left: 90px; right: 90px; top: 206px;
    list-style: none;
    display: grid; grid-template-columns: 1fr 1fr; grid-auto-flow: column;
    grid-template-rows: repeat(4, 30px); column-gap: 40px;
    border-top: 1px solid rgba(245,196,0,.5); padding-top: 24px;
  }
  .services li {
    font-size: 14px; font-weight: 700; letter-spacing: .6px;
    text-transform: uppercase; color: var(--yellow); white-space: nowrap;
  }
  .services li::before {
    content: ""; display: inline-block; width: 7px; height: 7px;
    background: var(--yellow); margin-right: 10px; vertical-align: 2px;
  }

  /* Front: dark grey on yellow */
  .card-front {
    left: 60px; top: 510px; width: 760px; height: 434px;
    background: var(--yellow);
  }
  .name-band { position: absolute; left: 0; top: 50px; width: 760px; height: 50px; }
  .person-name {
    position: absolute; left: 26px; top: 58px;
    font-weight: 700; font-size: 23px; letter-spacing: .5px;
    color: var(--yellow); text-transform: uppercase;
  }
  .person-title {
    position: absolute; left: 318px; top: 62px;
    font-weight: 700; font-size: 15px; color: var(--grey);
  }

  .contact-list { position: absolute; left: 0; top: 140px; width: 400px; }
  .contact-row { position: relative; display: flex; align-items: flex-start; }
  .contact-row .icon { width: 26px; height: 26px; margin-left: 28px; flex: none; }
  .contact-row .text {
    margin-left: 40px; font-size: 15px; line-height: 20px;
    font-weight: 600; color: var(--grey);
  }
  .contact-row .divider {
    position: absolute; left: 0; width: 92px; height: 1px; background: var(--rule);
  }
  .row-abn { height: 62px; }
  .row-abn .divider { top: 54px; }
  .row-phone { height: 62px; padding-top: 4px; }
  .row-phone .divider { top: 56px; }
  .row-email { height: 52px; padding-top: 6px; }
  .row-email .divider { top: 46px; }
  .row-web { padding-top: 6px; }

  .card-front .brand {
    position: absolute; right: 40px; bottom: 44px; gap: 14px;
  }
  .card-front .brand-mark { background: var(--grey); width: 28px; height: 28px; }
  .card-front .brand-name { font-size: 32px; color: var(--grey); text-align: right; }
</style>
</head>
<body>
<main class="canvas">

  <section class="card card-reverse" aria-label="Business card, reverse side">
    <div class="brand">
      <span class="brand-mark"></span>
      <span class="brand-name">Bright Oak Home Care</span>
    </div>
    <p class="web-address">www.brightoakhomecare.com.au</p>
    <ul class="services">
      <li>General Repairs</li>
      <li>Painting / Tiling</li>
      <li>Paving &amp; Concreting</li>
      <li>Pressure Washing</li>
      <li>On-Site Welding</li>
      <li>Decking Additions &amp; Repairs</li>
      <li>Fencing</li>
      <li>Full Bond Cleaning</li>
    </ul>
  </section>

  <section class="card card-front" aria-label="Business card, front side">
    <svg class="name-band" viewBox="0 0 760 50" aria-hidden="true">
      <path d="M0 0 H276 Q292 0 298 12 L310 34 H760 V50 H0 Z" fill="var(--grey)"/>
    </svg>
    <h1 class="person-name">Darren Holtwick</h1>
    <p class="person-title">Managing Director</p>

    <div class="contact-list">
      <div class="contact-row row-abn">
        <svg class="icon" viewBox="0 0 24 24" aria-hidden="true">
          <path d="M12 2 4 5v6c0 5 3.4 9.4 8 11 4.6-1.6 8-6 8-11V5z" fill="var(--grey)"/>
          <path d="M8 12l3 3 5-6" fill="none" stroke="var(--yellow)" stroke-width="2"/>
        </svg>
        <p class="text">ABN: 71 284 630 912<br>Fully Insured</p>
        <span class="divider"></span>
      </div>
      <div class="contact-row row-phone">
        <svg class="icon" viewBox="0 0 24 24" aria-hidden="true">
          <path d="M6.6 10.8a15 15 0 0 0 6.6 6.6l2.2-2.2c.3-.3.7-.4 1-.2 1.1.4 2.3.6 3.6.6.6 0 1 .4 1 1V20c0 .6-.4 1-1 1A17 17 0 0 1 3 4c0-.6.4-1 1-1h3.5c.6 0 1 .4 1 1 0 1.3.2 2.5.6 3.6.1.3 0 .7-.2 1z" fill="var(--grey)"/>
        </svg>
        <p class="text">0488 274 915<br>0488 274 915</p>
        <span class="divider"></span>
      </div>
      <div class="contact-row row-email">
        <svg class="icon" viewBox="0 0 24 24" aria-hidden="true">
          <path d="M2 5h20v14H2z" fill="var(--grey)"/>
          <path d="M2.5 5.5 12 13l9.5-7.5" fill="none" stroke="var(--yellow)" stroke-width="1.4"/>
        </svg>
        <p class="text">info@brightoakhomecare.com.au</p>
        <span class="divider"></span>
      </div>
      <div class="contact-row row-web">
        <svg class="icon" viewBox="0 0 24 24" aria-hidden="true">
          <g fill="none" stroke="var(--grey)" stroke-width="1.6">
            <circle cx="12" cy="12" r="9.5"/>
            <ellipse cx="12" cy="12" rx="4.2" ry="9.5"/>
            <path d="M2.5 12h19M4 7h16M4 17h16"/>
          </g>
        </svg>
        <p class="text">brightoakhomecare.com.au</p>
      </div>
    </div>

    <div class="brand">
      <span class="brand-mark"></span>
      <span class="brand-name">Bright Oak<br>Home Care</span>
    </div>
  </section>

</main>
</body>
</html>
```